Ductless Mini Split Business Website

Copper Fern Services is looking to design an eye catching educational website about installing Ductless mini splits.

Similar to this company.
https://www.halvikstream.com/

Coding

Coded - Design and coding required

```html
<!DOCTYPE html>
<html lang="en">
<head>
<meta charset="utf-8">
<title>Copper Fern Services – Ductless Experts</title>
<link href="https://fonts.googleapis.com/css2?family=Montserrat:wght@400;500;600;700;800&display=swap" rel="stylesheet">
<style>
:root{
  --yellow:#fbc110;
  --yellow-deep:#e8a900;
  --ink:#1d1d1f;
  --dark:#202124;
  --text:#444;
  --muted:#6b6b6b;
  --light:#f1f1f1;
  --white:#fff;
}
*{margin:0;padding:0;box-sizing:border-box}
html,body{width:1200px;height:4461px;overflow:hidden}
body{font-family:"Montserrat",sans-serif;color:var(--text);background:var(--white);position:relative}
.abs{position:absolute}
h2.section-title{font-size:44px;font-weight:600;color:var(--ink);letter-spacing:.5px}
.bar{display:block;width:40px;height:5px;background:var(--yellow);border-radius:2px}

/* header */
.brand{left:95px;top:14px;width:280px}
.brand-name{display:flex;align-items:center;gap:10px;font-size:26px;font-weight:700;color:var(--ink)}
.brand-name i{width:30px;height:30px;border-radius:50%;background:var(--yellow);display:block}
.brand-tag{font-size:17px;font-weight:700;color:var(--ink);margin-top:10px;margin-left:4px}
.topbar{left:390px;top:0;width:555px;height:42px;background:var(--dark);display:flex;align-items:center;padding-left:50px;color:#fff;font-weight:600;font-size:20px;gap:14px}
.topbar .soc{display:flex;gap:22px;margin-left:70px}
.topbar .soc span{width:14px;height:14px;border-radius:50%;background:#fff;display:block}
.request{left:945px;top:0;width:255px;height:42px;background:var(--yellow);color:var(--ink);font-weight:600;font-size:15px;display:flex;align-items:center;justify-content:center}
.nav{left:417px;top:66px;display:flex;gap:37px;font-size:13px;font-weight:500;color:var(--ink)}
.nav .on{position:relative}
.nav .on::after{content:"";position:absolute;left:-6px;right:-6px;bottom:-12px;height:3px;background:var(--yellow)}
.infobar{left:0;top:100px;width:1200px;height:68px;background:#f0f0f0;display:flex;border-top:1px solid #e2e2e2}
.info{flex:1;display:flex;align-items:center;gap:18px;padding-left:86px;border-right:1px solid #ddd;font-size:13px}
.info:nth-child(2){padding-left:35px}.info:nth-child(3){padding-left:40px}.info:nth-child(4){padding-left:40px;border:0}
.info b{display:block;font-weight:600;color:var(--ink);font-size:13px}
.info small{font-size:12px;color:#333}

/* hero */
.hero{left:0;top:168px;width:1200px;height:507px;background:linear-gradient(100deg,#d9d3ca 0%,#c8beb2 45%,#b9b0a4 100%)}
.hero-card{left:65px;top:82px;width:515px;height:275px;background:var(--yellow);border-radius:34px;border-left:10px solid #1a1a1a;padding:48px 0 0 55px}
.hero-card h1{font-size:44px;font-weight:700;color:#fff;letter-spacing:1px;white-space:nowrap}
.hero-card p{font-size:21px;color:#fff;margin-top:12px}
.btn-dark{display:inline-block;margin-top:32px;background:#1b1b1b;color:#fff;font-weight:600;font-size:16px;padding:16px 24px;border-radius:28px}
.dots{left:553px;top:438px;display:flex;gap:14px}
.dots i{width:10px;height:10px;border-radius:50%;background:var(--yellow);display:block}

/* about */
.about{left:57px;top:765px;width:520px}
.about p{font-size:15px;line-height:37px;margin-top:30px}
.btn-yellow{display:inline-block;margin-top:38px;background:var(--yellow);color:var(--ink);font-weight:700;font-size:16px;padding:15px 34px;border-radius:28px}
.about-img{left:640px;top:740px;width:560px;height:390px}

/* why */
.why{left:0;top:1258px;width:1200px;height:655px;background:linear-gradient(180deg,#2e2e30,#1b1b1c)}
.why h2{color:#fff;text-align:center;margin-top:88px}
.why .bar{margin:20px auto 0}
.circle{width:320px;height:320px;border-radius:50%;top:218px;display:flex;flex-direction:column;align-items:center;justify-content:center;text-align:center;padding:0 40px}
.circle.y{background:radial-gradient(circle,var(--yellow) 62%,#d09b00 63%,#d09b00 70%,var(--yellow) 71%)}
.circle.d{background:#232325;box-shadow:0 0 0 12px #1a1a1b}
.circle h3{font-size:19px;font-weight:600;color:var(--ink);line-height:25px;margin-top:14px}
.circle.d h3{color:#fff;font-size:24px;line-height:31px}
.circle p{font-size:14px;line-height:26px;margin-top:12px;color:var(--ink)}
.circle.d p{color:#ddd}
.circle svg{width:56px;height:56px}

/* stand */
.stand-img{left:0;top:2010px;width:520px;height:385px}
.stand{left:614px;top:2028px;width:560px}
.stand h2{line-height:52px}
.stand .bar{margin-top:22px}
.stand ul{list-style:none;margin-top:26px}
.stand li{display:flex;gap:20px;font-size:15px;color:#333;height:37.5px;align-items:center}
.stand li svg{width:14px;height:14px;flex:none}

/* services */
.help h2{text-align:center}
.tile{width:240px;height:302px;border-radius:2px;overflow:hidden}
.tile span{position:absolute;left:16px;bottom:20px;color:#fff;font-size:18px;font-weight:500;line-height:27px;width:150px}
.tile svg{position:absolute;right:18px;bottom:22px;width:26px;height:8px}

/* testimonials */
.testi{left:0;top:3337px;width:1200px;height:588px;background:var(--light)}
.testi h2{text-align:center;margin-top:90px}
.testi .bar{margin:22px auto 0}
.card{top:236px;width:320px;height:245px;background:#fff;border-radius:26px;padding:48px 34px 0;box-shadow:0 8px 18px rgba(0,0,0,.05)}
.quote{position:absolute;left:34px;top:-26px;width:50px;height:50px;background:var(--yellow);display:flex;align-items:center;justify-content:center;color:var(--ink);font-size:42px;font-weight:800;line-height:1}
.card h4{font-size:22px;font-weight:600;color:var(--ink)}
.card p{font-size:13px;line-height:27px;margin-top:12px;color:var(--muted)}
.card a{display:inline-block;margin-top:12px;font-size:13px;font-weight:600;color:var(--yellow);text-decoration:underline}
.arrow{font-size:28px;color:#555;top:3687px}

/* footer */
.foot{left:0;top:3925px;width:1200px;height:536px;background:#1b1b1c;color:#fff}
.news{left:124px;top:70px;font-size:30px;font-weight:500}
.subscribe{left:536px;top:71px;display:flex;height:44px}
.subscribe div{width:404px;background:#fff;color:#999;font-size:12px;display:flex;align-items:center;padding-left:16px}
.subscribe b{width:135px;background:var(--yellow);color:var(--ink);font-size:14px;display:flex;align-items:center;justify-content:center}
.fcol{top:223px;font-size:13px}
.fcol h5{font-size:17px;font-weight:600;margin-bottom:20px}
.fcol li{list-style:none;line-height:27px;color:#ddd}
.socials{left:505px;top:438px;display:flex;gap:12px}
.socials i{width:40px;height:40px;border-radius:50%;background:var(--yellow);display:block}
.copy{left:0;top:500px;width:1200px;text-align:center;font-size:12px;color:#ddd}
</style>
</head>
<body>

<!-- header -->
<div class="abs brand">
  <div class="brand-name"><i></i>Copper Fern</div>
  <div class="brand-tag">DUCTLESS EXPERTS</div>
</div>
<div class="abs topbar">
  <svg width="16" height="16" viewBox="0 0 24 24"><path fill="#fff" d="M6.6 10.8a15 15 0 0 0 6.6 6.6l2.2-2.2c.3-.3.7-.4 1-.2 1.1.4 2.3.6 3.6.6.6 0 1 .4 1 1V20c0 .6-.4 1-1 1A17 17 0 0 1 3 4c0-.6.4-1 1-1h3.5c.6 0 1 .4 1 1 0 1.3.2 2.5.6 3.6.1.3 0 .7-.2 1z"/></svg>
  +1 555-014-2297
  <div class="soc"><span></span><span></span><span></span><span></span></div>
</div>
<div class="abs request">REQUEST INFO</div>
<nav class="abs nav">
  <span class="on">HOME</span><span>ABOUT US</span><span>DUCTLESS EXPERTS</span><span>FAQ</span><span>FINANCING</span><span>REVIEWS</span><span>CONTACT US</span>
</nav>
<div class="abs infobar">
  <div class="info"><svg width="32" height="32" viewBox="0 0 24 24" fill="none" stroke="#555" stroke-width="1.2"><path d="M12 21s-6-6-6-11a6 6 0 0 1 12 0c0 5-6 11-6 11z"/><circle cx="12" cy="10" r="2.2"/></svg><div><b>Visit our Location</b><small>Sed ut perspiciatis unde omnis</small></div></div>
  <div class="info"><svg width="32" height="32" viewBox="0 0 24 24" fill="none" stroke="#555" stroke-width="1.2"><path d="M6.6 10.8a15 15 0 0 0 6.6 6.6l2.2-2.2 4.6 1.6V20A17 17 0 0 1 3 4h3.5l1.6 4.6z"/></svg><div><b>Call Us Now</b><small>+1 555-014-2297</small></div></div>
  <div class="info"><svg width="40" height="32" viewBox="0 0 30 24" fill="none" stroke="#555" stroke-width="1.2"><rect x="9" y="5" width="19" height="14"/><path d="M9 5l9.5 8L28 5M1 9h6M3 13h4M1 17h6"/></svg><div><b>Send Email</b><small>hello@copperfern.example</small></div></div>
  <div class="info"><svg width="32" height="32" viewBox="0 0 24 24" fill="none" stroke="#555" stroke-width="1.2"><circle cx="12" cy="12" r="9"/><path d="M12 7v5l3 2"/></svg><div><b>Opening Hours</b><small>Mon - Fri : 8.30 to 7.00 pm</small></div></div>
</div>

<!-- hero -->
<section class="abs hero" role="img" aria-label="Woman relaxing on a sofa under a wall-mounted ductless air conditioner in a bright living room">
  <div class="abs hero-card">
    <h1>COPPER FERN SERVICES</h1>
    <p>Ductless Experts</p>
    <span class="btn-dark">GET STARTED</span>
  </div>
  <div class="abs dots"><i></i><i></i><i></i><i></i></div>
</section>

<!-- about -->
<section class="abs about">
  <h2 class="section-title">About Us</h2>
  <span class="bar" style="margin-top:22px"></span>
  <p>Lorem ipsum dolor sit amet, consectetur adipiscing elit, sed do eiusmod tempor incididunt ut labore et dolore magna aliqua. Ut enim ad minim veniam, quis nostrud exercitation ullamco laboris nisi ut aliquip ex ea commodo consequat.</p>
  <span class="btn-yellow">READ MORE</span>
</section>
<svg class="abs about-img" viewBox="0 0 560 390">
  <path d="M80 20 L560 0 L560 12 L92 30 Q60 32 50 70 L8 360 Q6 372 18 380 L10 382 Q-4 372 0 356 L40 62 Q48 24 80 20z" fill="#fbc110"/>
  <path d="M100 40 L560 22 L560 390 L60 390 Q34 388 38 360 L68 80 Q74 42 100 40z" fill="#cfc6bb" role="img" aria-label="Technician installing a ductless indoor unit on a wall"/>
</svg>

<!-- why -->
<section class="abs why">
  <h2 class="section-title">Why Choose Us</h2>
  <span class="bar"></span>
  <div class="abs circle y" style="left:148px">
    <svg viewBox="0 0 48 48" fill="none" stroke="#1d1d1f" stroke-width="2"><rect x="8" y="12" width="32" height="18" rx="2"/><circle cx="24" cy="21" r="5"/><path d="M6 36h36"/></svg>
    <h3>365 Day, Money Back Guarantee</h3>
    <p>Lorem ipsum dolor sit amet, consectetur adipiscing</p>
  </div>
  <div class="abs circle d" style="left:434px;top:208px">
    <svg viewBox="0 0 48 48" fill="none" stroke="#fff" stroke-width="2"><path d="M18 8h12l-3 6h-6z"/><circle cx="24" cy="26" r="10"/><path d="M24 20v12M21 23h5M21 29h5"/></svg>
    <h3>0% Financing for 60 months</h3>
    <p>Lorem ipsum dolor sit amet, consectetur adipiscing</p>
  </div>
  <div class="abs circle y" style="left:728px">
    <svg viewBox="0 0 48 48" fill="none" stroke="#1d1d1f" stroke-width="2"><path d="M14 18a10 10 0 0 1 20 0z"/><path d="M10 42a14 10 0 0 1 28 0"/><path d="M16 20v4a8 8 0 0 0 16 0v-4"/></svg>
    <h3>We Are the Experts in Ductless Services</h3>
    <p>Lorem ipsum dolor sit amet, consectetur adipiscing</p>
  </div>
</section>

<!-- stand behind -->
<svg class="abs stand-img" viewBox="0 0 520 385">
  <path d="M0 0 L430 14 Q460 16 466 50 L520 350 L506 352 L452 52 Q446 26 420 26 L0 14z" fill="#fbc110"/>
  <path d="M0 22 L412 34 Q438 36 444 62 L496 340 Q500 385 450 385 L0 385z" fill="#d8d2ca" role="img" aria-label="Woman on a sofa using a remote to adjust a ductless unit"/>
</svg>
<section class="abs stand">
  <h2 class="section-title">We Stand Behind Our Ductless Services</h2>
  <span class="bar"></span>
  <ul>
    <li><svg viewBox="0 0 14 14"><path d="M1 7l4 4 8-9" fill="none" stroke="#fbc110" stroke-width="2.4"/></svg>Sed ut perspiciatis unde omnis iste natus error</li>
    <li><svg viewBox="0 0 14 14"><path d="M1 7l4 4 8-9" fill="none" stroke="#fbc110" stroke-width="2.4"/></svg>Lorem ipsum dolor sit amet, consectetur adipiscing elit, sed do</li>
    <li><svg viewBox="0 0 14 14"><path d="M1 7l4 4 8-9" fill="none" stroke="#fbc110" stroke-width="2.4"/></svg>Excepteur sint occaecat cupidatat non proident</li>
    <li><svg viewBox="0 0 14 14"><path d="M1 7l4 4 8-9" fill="none" stroke="#fbc110" stroke-width="2.4"/></svg>Sed ut perspiciatis unde</li>
    <li><svg viewBox="0 0 14 14"><path d="M1 7l4 4 8-9" fill="none" stroke="#fbc110" stroke-width="2.4"/></svg>But I must explain to you how all this mistaken idea</li>
    <li><svg viewBox="0 0 14 14"><path d="M1 7l4 4 8-9" fill="none" stroke="#fbc110" stroke-width="2.4"/></svg>Lorem ipsum dolor sit amet, consectetur adipiscing</li>
  </ul>
</section>

<!-- services -->
<section class="help">
  <h2 class="abs section-title" style="left:0;top:2485px;width:1200px">How Can We Help You?</h2>
  <div class="abs tile" style="left:90px;top:2606px;background:linear-gradient(180deg,#8d9aa6,#4a4f55)" role="img" aria-label="Technician servicing an outdoor heat pump"><span>Baseboard Heat Replacement</span><svg viewBox="0 0 26 8"><path d="M0 4h24M20 1l4 3-4 3" stroke="#fff" fill="none"/></svg></div>
  <div class="abs tile" style="left:350px;top:2606px;background:linear-gradient(180deg,#b7aa98,#4d463f)" role="img" aria-label="Technician working on indoor equipment"><span style="width:200px">Ductless For Additions &amp; Remodels</span><svg viewBox="0 0 26 8"><path d="M0 4h24M20 1l4 3-4 3" stroke="#fff" fill="none"/></svg></div>
  <div class="abs tile" style="left:610px;top:2606px;background:linear-gradient(180deg,#9aa7b3,#3e4247)" role="img" aria-label="Pressure gauges connected to a heat pump"><span>Ductless Heat Pump Faq</span><svg viewBox="0 0 26 8"><path d="M0 4h24M20 1l4 3-4 3" stroke="#fff" fill="none"/></svg></div>
  <div class="abs tile" style="left:870px;top:2606px;background:linear-gradient(180deg,#dcd8d3,#5a6b84)" role="img" aria-label="Installer mounting an indoor unit on a brick wall"><span>Ductless Installation</span><svg viewBox="0 0 26 8"><path d="M0 4h24M20 1l4 3-4 3" stroke="#fff" fill="none"/></svg></div>
  <div class="abs tile" style="left:90px;top:2930px;background:linear-gradient(180deg,#7d7468,#2d2b29)" role="img" aria-label="Technician inspecting unit wiring"><span>Ductless Maintenance</span><svg viewBox="0 0 26 8"><path d="M0 4h24M20 1l4 3-4 3" stroke="#fff" fill="none"/></svg></div>
  <div class="abs tile" style="left:350px;top:2930px;background:linear-gradient(180deg,#e4e6e8,#5d6d80)" role="img" aria-label="Technician repairing an open indoor unit"><span>Ductless Repairs</span><svg viewBox="0 0 26 8"><path d="M0 4h24M20 1l4 3-4 3" stroke="#fff" fill="none"/></svg></div>
  <div class="abs tile" style="left:610px;top:2930px;background:linear-gradient(180deg,#eceef0,#6c7580)" role="img" aria-label="Woman relaxing on a sofa below an air conditioner"><span>Ductless Warranty</span><svg viewBox="0 0 26 8"><path d="M0 4h24M20 1l4 3-4 3" stroke="#fff" fill="none"/></svg></div>
  <div class="abs tile" style="left:870px;top:2930px;background:linear-gradient(180deg,#e2ddd8,#55504c)" role="img" aria-label="Couple relaxing on a sofa in a cool room"><span>Whole House Ductless</span><svg viewBox="0 0 26 8"><path d="M0 4h24M20 1l4 3-4 3" stroke="#fff" fill="none"/></svg></div>
</section>

<!-- testimonials -->
<section class="abs testi">
  <h2 class="section-title">Testimonials</h2>
  <span class="bar"></span>
  <div class="abs card" style="left:90px"><div class="quote">“</div><h4>Samantha J</h4><p>Lorem ipsum dolor sit amet, ting elit, sed do eiusmod tdunt ut labore et dolore magna aliqua. Ut enim ad minim veniam,</p><a>READ MORE</a></div>
  <div class="abs card" style="left:440px"><div class="quote">“</div><h4>Helen C</h4><p>Lorem ipsum dolor sit amet, ting elit, sed do eiusmod tdunt ut labore et dolore magna aliqua. Ut enim ad minim veniam,</p><a>READ MORE</a></div>
  <div class="abs card" style="left:790px"><div class="quote">“</div><h4>Jann O</h4><p>Lorem ipsum dolor sit amet, ting elit, sed do eiusmod tdunt ut labore et dolore magna aliqua. Ut enim ad minim veniam,</p><a>READ MORE</a></div>
</section>
<div class="abs arrow" style="left:34px">‹</div>
<div class="abs arrow" style="left:1148px">›</div>

<!-- footer -->
<footer class="abs foot">
  <div class="abs news">Subscribe Our Newsletter</div>
  <div class="abs subscribe"><div>Enter Your Email Id</div><b>SUBSCRIBE</b></div>
  <div class="abs fcol" style="left:118px"><h5>QUICK LINKS</h5><ul><li>Home</li><li>About Us</li><li>Ductless</li><li>Experts</li><li>Faq</li></ul></div>
  <div class="abs fcol" style="left:340px;top:266px"><ul><li>Financing</li><li>Reviews</li><li>Contact Us</li></ul></div>
  <div class="abs fcol" style="left:553px"><h5>OTHER LINKS</h5><ul><li>Terms &amp; Policy</li><li>Sitemap</li><li>Acceptable Use</li><li>Conditions</li></ul></div>
  <div class="abs fcol" style="left:834px;width:230px"><h5>CONTACT US</h5><ul><li>482 Larkspur Ave. Eastvale, CA 90000</li><li>(555) 014-7731</li><li>hello@copperfern.example</li></ul></div>
  <div class="abs socials"><i></i><i></i><i></i><i></i></div>
  <div class="abs copy">© Copyrights 2019 The Company Name All Rights Reserved</div>
</footer>

</body>
</html>
```